Fresh, modern, fun business card for pediatric dental practice

Need a business card for fresh, modern, fun pediatric dental practice

Clean look that matches our website's font and colors

We prefer the look of curved corners on business cards

Target Market(s)

parents (mothers) of young children, professionals, mid-high class

Industry/Entity Type

Dental

Contact Information for Business Card

Maplebrook Pediatric Dentistry
482 Quarry Lane
Suite 517
Fernhollow, Westmark 00417
555.555.0193
www.maplebrookkidsdental.example

Mei-Ran Tsai, DMD
Corinne Walbeck, DMD
(we are working on our email address, but we would like that on the card as well)

Font styles to use
Sans Serif

Requirements
Must have
• All info; we would also like to make cards for individual staff members
• colors from our website and color palatte, attatched
• use same font and design as website for branding
Nice to have
• clean, simple card that has a pop of color
• we would like to see a few designs with our tag line "where smiles get brighter"
• we are not sure if we want to have it on there or not
• we would like to see a few designs incorporating the ribbon graphic on our website where the word WELCOME is

```html
<!DOCTYPE html>
<html lang="en">
<head>
<meta charset="utf-8">
<title>Maplebrook Pediatric Dentistry – Business Card</title>
<link rel="stylesheet" href="https://fonts.googleapis.com/css2?family=Source+Sans+3:wght@400;600;700&display=swap">
<style>
  :root {
    --page: #d9d6d3;
    --card: #2a2729;
    --yellow: #f6b21b;
    --magenta: #d3329b;
    --white: #f4f2f2;
  }
  * { box-sizing: border-box; margin: 0; padding: 0; }
  html, body {
    width: 1200px; height: 844px; overflow: hidden;
    background: var(--page);
    font-family: "Source Sans 3", sans-serif;
  }
  .stage {
    width: 1200px; height: 844px;
    display: flex; align-items: center; justify-content: center; gap: 60px;
  }
  .card {
    position: relative;
    width: 525px; height: 300px;
    background: var(--card);
    border-radius: 6px;
    overflow: hidden;
    box-shadow: 0 6px 18px rgba(0,0,0,.25);
  }
  /* Back: contact side */
  .band { position: absolute; left: 0; right: 0; height: 14px; }
  .band--top { top: 24px; background: var(--yellow); }
  .band--bottom { bottom: 24px; background: var(--magenta); }
  .contact {
    position: absolute; left: 0; right: 0; top: 60px;
    text-align: center; color: var(--white);
    font-size: 14px; line-height: 1.32;
  }
  .contact__names { font-weight: 700; font-size: 16px; line-height: 1.2; margin-bottom: 12px; }
  .contact__degree { color: var(--yellow); }
  .contact__lines { margin-bottom: 12px; }
  .contact__label { color: var(--magenta); font-weight: 700; }
  /* Front: name side */
  .tab {
    position: absolute; width: 24px; height: 36px;
    background: var(--yellow);
  }
  .tab--right { top: 22px; right: 0; border-left: 4px solid var(--magenta); }
  .tab--left { top: 150px; left: 0; border-right: 4px solid var(--magenta); }
  .brand {
    position: absolute; inset: 0;
    display: flex; flex-direction: column; align-items: center; justify-content: center;
    color: var(--yellow); font-weight: 700; text-align: center;
  }
  .brand__name { font-size: 52px; line-height: 1; letter-spacing: .5px; }
  .brand__sub { font-size: 26px; line-height: 1.2; margin-top: 4px; }
</style>
</head>
<body>
<main class="stage">
  <section class="card card--back" aria-label="Card back with contact details">
    <div class="band band--top"></div>
    <div class="contact">
      <p class="contact__names">
        Mei-Ran Tsai, <span class="contact__degree">DMD</span><br>
        Corinne Walbeck, <span class="contact__degree">DMD</span>
      </p>
      <p class="contact__lines">
        <span class="contact__label">P:</span> 555.555.0193<br>
        <span class="contact__label">E:</span> Mei-ran@maplebrookkidsdental.example<br>
        <span class="contact__label">E:</span> Corinne@maplebrookkidsdental.example<br>
        <span class="contact__label">W:</span> www.maplebrookkidsdental.example
      </p>
      <p class="contact__address">
        Maplebrook Pediatric Dentistry<br>
        482 Quarry Lane Suite 517<br>
        Fernhollow, Westmark 00417
      </p>
    </div>
    <div class="band band--bottom"></div>
  </section>

  <section class="card card--front" aria-label="Card front with practice name">
    <div class="tab tab--right"></div>
    <div class="tab tab--left"></div>
    <div class="brand">
      <span class="brand__name">Maplebrook</span>
      <span class="brand__sub">Pediatric Dentistry</span>
    </div>
  </section>
</main>
</body>
</html>
```